High-end law practice specializing in closely held business succession planning and complex estates

Solo practitioner whose practice specializes in high-net worth, complex estate planning needs muliple versions of letterhead black and white, please. Letterhead should incorporate slogan, "Protecting your family business is my business," for one and "Complex Estate Planning"; third with no slogan. All for The Law Office of Marcy Lynn Pettibone, PC, 418 Cedar Hollow Ln., Newport News, Virginia 23648, Tel. 757-555-0142 Fax tbd email: marcy@mlplawgroup.example; Marcy Lynn Pettibone, Esq., principal, licensed in VA, NY, DC
Updates

Project Deadline Extended
Reason: My internet service went down and I can only view designs on my smart phone -- it's just too hard to review. So sorry! Working with my ISP now. Please be patient!

Target Market(s)

High net worth clients with complex estate planning needs, family businesses, family farmers, family foresters -- people with unique estate/succession planning needs who need a specialist who understands them.

Industry/Entity Type

Business

Font styles to use
Script

Requirements
Must have
• A high-end look and feel, connoting trustworthiness, special knowledge, and expertise.

```html
<!DOCTYPE html>
<html lang="en">
<head>
<meta charset="UTF-8">
<title>Letterhead – The Law Office of Marcy Lynn Pettibone, PC</title>
<link rel="stylesheet" href="https://fonts.googleapis.com/css2?family=Libre+Baskerville:ital,wght@0,400;0,700;1,400&family=Arimo:wght@400&display=swap">
<style>
  :root {
    --backdrop: #e8e8e8;
    --paper: #ffffff;
    --ink: #111111;
    --band: #050505;
    --band-text: #ffffff;
    --rule: #333333;
  }
  html, body {
    margin: 0;
    padding: 0;
    width: 1200px;
    height: 936px;
    overflow: hidden;
    background: var(--backdrop);
  }
  .letterhead {
    position: absolute;
    left: 289px;
    top: 28px;
    width: 622px;
    height: 880px;
    background: var(--paper);
    box-shadow: 0 2px 10px rgba(0,0,0,0.12);
    color: var(--ink);
  }
  .contact {
    position: absolute;
    right: 40px;
    top: 30px;
    text-align: right;
    font-family: "Arimo", Arial, sans-serif;
    font-size: 10px;
    line-height: 13px;
  }
  .contact p { margin: 0; }
  .header-rule {
    position: absolute;
    left: 200px;
    right: 40px;
    top: 72px;
    height: 0;
    border-top: 1px solid var(--rule);
  }
  .address {
    position: absolute;
    right: 40px;
    top: 76px;
    text-align: right;
    font-family: "Arimo", Arial, sans-serif;
    font-size: 10px;
    line-height: 13px;
  }
  .address p { margin: 0; }
  .firm {
    position: absolute;
    left: 40px;
    top: 62px;
  }
  .firm-name {
    margin: 0;
    font-family: "Libre Baskerville", Georgia, serif;
    font-weight: 700;
    font-size: 14px;
    line-height: 17px;
    text-transform: uppercase;
    letter-spacing: 0.2px;
  }
  .firm-focus {
    margin: 2px 0 0;
    font-family: "Libre Baskerville", Georgia, serif;
    font-style: italic;
    font-size: 12.5px;
  }
  .slogan {
    position: absolute;
    right: 40px;
    bottom: 48px;
    margin: 0;
    font-family: "Arimo", Arial, sans-serif;
    font-size: 12px;
  }
  .footer-band {
    position: absolute;
    left: 0;
    right: 0;
    bottom: 0;
    height: 40px;
    background: var(--band);
    color: var(--band-text);
    font-family: "Arimo", Arial, sans-serif;
    font-size: 12.5px;
    text-transform: uppercase;
    display: flex;
    align-items: center;
    justify-content: flex-end;
    padding-right: 40px;
    box-sizing: border-box;
  }
</style>
</head>
<body>
  <main class="letterhead">
    <div class="contact">
      <p>757-555-0142</p>
      <p>757-555-0199</p>
      <p>marcy@mlplawgroup.example</p>
    </div>
    <div class="header-rule"></div>
    <div class="address">
      <p>418 Cedar Hollow Ln., Newport News,</p>
      <p>Virginia 23648</p>
    </div>
    <header class="firm">
      <h1 class="firm-name">The Law Office<br>of Marcy Lynn Pettibone, PC</h1>
      <p class="firm-focus">Complex Estate Planning</p>
    </header>
    <p class="slogan">Protecting Your Family Business is my Business</p>
    <footer class="footer-band">Marcy Lynn Pettibone, Esq., Principal, Licensed in VA, NY, DC</footer>
  </main>
</body>
</html>
```